Digital Recipe eBook Design

I need a recipe eBook designed for me. I have attached the recipes (see here https://pages.tarnovel.net/sheet/k/7Qp3XZ41TTb82Lr5mkdBvxhpJQ0NsoRPYcEAK63FXwtu/view?mode=public) and associated images in Google Drive (see images here https://store.plumvexa.com/store/bundles/83KTsQwund5Ho2Pcm6yvbrEXk0TZ?mode=public). I am open to any sort of ideas but want the recipe book to look highly professional and with a simple, yet sleek, design. I have included some examples of designs I like here: https://store.plumvexa.com/store/bundles/6R_Ty4GDqJpsm-NnbwuhLoEC0PZBk?mode=public

Target Market(s)

Women 20-35

Industry/Entity Type

Health And Wellness

Font styles to use
Sans Serif

Colors
e667a6
eea4c8
f9deeb

Requirements
Must have
• No typos
• Professional design
Should not have
• Overly decorative design - keep it simple and clean

```html
<!DOCTYPE html>
<html lang="en">
<head>
<meta charset="utf-8">
<title>The Balanced Glow Cookbook – Cover Concepts</title>
<link rel="stylesheet" href="https://fonts.googleapis.com/css2?family=Quicksand:wght@300;400;500;700&family=Montserrat:wght@500;600;700&display=swap">
<style>
  :root {
    --pink-deep: #e667a6;
    --pink-mid: #eea4c8;
    --pink-soft: #f9deeb;
    --pink-band: #eeb0cc;
    --pink-band-strong: #eaa2c7;
    --white: #ffffff;
    --page: #ffffff;
  }
  * { box-sizing: border-box; margin: 0; padding: 0; }
  html, body { width: 1200px; height: 675px; overflow: hidden; background: var(--page); }
  .canvas { position: relative; width: 1200px; height: 675px; }

  .cover {
    position: absolute; top: 163px; height: 328px; overflow: hidden;
    background: var(--white);
    box-shadow: 0 1px 5px rgba(0,0,0,0.18);
  }
  .cover--grid { left: 59px; width: 252px; height: 327px; }
  .cover--classic { left: 332px; width: 255px; }
  .cover--hero { left: 606px; width: 255px; }
  .cover--panel { left: 882px; width: 254px; }

  .band {
    position: absolute; left: 0; right: 0; background: var(--pink-band);
    color: var(--white); font-family: "Quicksand", sans-serif; font-weight: 700;
    font-size: 8.5px; letter-spacing: 1.7px; text-align: center;
    display: flex; align-items: center; justify-content: center;
  }
  .band--top { top: 0; height: 23px; }
  .band--bottom { bottom: 0; height: 23px; }
  .band--strong { background: var(--pink-band-strong); }

  .photo { position: absolute; }
  /* food photography areas: main tones of each dish */
  .tone-berry   { background: linear-gradient(135deg, #8da3bd 0%, #5b4038 45%, #2f3f66 100%); }
  .tone-cacao   { background: linear-gradient(180deg, #c9c2ba 0%, #6b4228 55%, #f1eeea 100%); }
  .tone-cracker { background: linear-gradient(135deg, #b49a74 0%, #7a5a3a 50%, #e6d8c6 100%); }
  .tone-bread   { background: linear-gradient(160deg, #5f7c99 0%, #a9824f 55%, #d9cbb4 100%); }
  .tone-bowl    { background: linear-gradient(135deg, #b52b4a 0%, #6d86a6 45%, #e8962a 100%); }
  .tone-juice   { background: linear-gradient(180deg, #c9c8d0 0%, #9bbd3a 55%, #6f8f2a 100%); }
  .tone-slice   { background: linear-gradient(160deg, #ddd8d4 0%, #3e2420 45%, #c98798 100%); }
  .tone-salad   { background: linear-gradient(135deg, #8a7458 0%, #5f943a 55%, #d8d4c8 100%); }
  .tone-tea     { background: linear-gradient(160deg, #f2f3ee 0%, #e0d8c2 55%, #d4a63a 100%); }
  .tone-veg     { background: linear-gradient(135deg, #6a2f62 0%, #d9522a 45%, #d9b57a 60%, #4f8a34 100%); }
  .tone-bites   { background: linear-gradient(160deg, #f4f1ea 0%, #e5c463 60%, #d7ad3d 100%); }
  .tone-bites-large {
    background: linear-gradient(150deg, #f7f3ec 0%, #efe3c2 30%, #e4c464 55%, #d8ad42 72%, #c79a6a 88%, #f2ece4 100%);
  }

  .badge {
    position: absolute; border-radius: 50%; background: var(--pink-mid);
    color: var(--white); font-family: "Quicksand", sans-serif; font-weight: 400;
    display: flex; align-items: center; justify-content: center; text-align: center;
  }
  .cover--grid .badge { left: 70px; top: 69px; width: 114px; height: 114px; font-size: 16.5px; line-height: 1.5; background: #efb1cf; }
  .cover--classic .badge { left: 75px; top: 132px; width: 106px; height: 106px; font-size: 13.5px; line-height: 1.45; }
  .cover--hero .badge { left: 72px; top: 100px; width: 112px; height: 112px; font-size: 14.5px; line-height: 1.45; }
  .cover--panel .badge { left: 5px; top: 1px; width: 78px; height: 78px; font-size: 9.5px; line-height: 1.55; }

  .title-spaced {
    position: absolute; left: 0; right: 0; top: 36px; text-align: center;
    font-family: "Quicksand", sans-serif; font-weight: 700; color: var(--pink-deep);
    font-size: 14px; letter-spacing: 6.5px; line-height: 19px; opacity: 0.85;
  }

  .title-strip {
    position: absolute; left: 17px; top: 12px; width: 224px; height: 28px;
    background: var(--white); border-radius: 2px;
    font-family: "Quicksand", sans-serif; font-weight: 700; color: var(--pink-deep);
    font-size: 13.5px; display: flex; align-items: center; justify-content: center;
  }

  .info-panel {
    position: absolute; left: 131px; top: 171px; width: 123px; height: 157px;
    background: var(--pink-mid); color: var(--white); text-align: center;
    font-family: "Montserrat", sans-serif;
  }
  .info-panel__kicker { margin-top: 10px; font-size: 5.5px; font-weight: 700; letter-spacing: 1px; }
  .info-panel__rule { margin: 8px 8px 0; border-top: 1.5px dotted var(--white); }
  .info-panel__title {
    margin-top: 12px; font-family: "Montserrat", sans-serif; font-weight: 600;
    color: var(--pink-deep); font-size: 15.5px; line-height: 18px;
  }
  .info-panel__rule--lower { margin-top: 12px; }
  .info-panel__byline { margin-top: 9px; font-size: 5.5px; font-weight: 700; letter-spacing: 1px; }
</style>
</head>
<body>
<main class="canvas">

  <section class="cover cover--grid">
    <div class="band band--top">The Balanced Glow Cookbook</div>
    <div class="photo tone-berry" style="left:0;top:23px;width:85px;height:62px" role="img" aria-label="Chia pudding cups topped with blueberries"></div>
    <div class="photo tone-cacao" style="left:85px;top:23px;width:85px;height:62px" role="img" aria-label="Cacao bliss balls on a plate"></div>
    <div class="photo tone-cracker" style="left:170px;top:23px;width:82px;height:62px" role="img" aria-label="Seed crackers on baking paper"></div>
    <div class="photo tone-bread" style="left:0;top:85px;width:85px;height:80px" role="img" aria-label="Sliced seeded loaf"></div>
    <div class="photo tone-cacao" style="left:85px;top:85px;width:85px;height:80px" role="img" aria-label="Cacao bites on a plate"></div>
    <div class="photo tone-bowl" style="left:170px;top:85px;width:82px;height:80px" role="img" aria-label="Smoothie bowls with fruit"></div>
    <div class="photo tone-juice" style="left:0;top:165px;width:85px;height:80px" role="img" aria-label="Green juices in bottles"></div>
    <div class="photo tone-slice" style="left:85px;top:165px;width:85px;height:80px" role="img" aria-label="Chocolate berry slices"></div>
    <div class="photo tone-salad" style="left:170px;top:165px;width:82px;height:80px" role="img" aria-label="Green salad in a bowl"></div>
    <div class="photo tone-tea" style="left:0;top:245px;width:85px;height:59px" role="img" aria-label="Cup of tea with flowers"></div>
    <div class="photo tone-veg" style="left:85px;top:245px;width:85px;height:59px" role="img" aria-label="Dip with vegetable sticks"></div>
    <div class="photo tone-bites" style="left:170px;top:245px;width:82px;height:59px" role="img" aria-label="Coconut bliss balls in a jar"></div>
    <div class="badge">Rooted<br>Whole<br>Wellness</div>
    <div class="band band--bottom">Lia Marsh</div>
  </section>

  <section class="cover cover--classic">
    <h1 class="title-spaced">The<br>Balanced Glow<br>Cookbook</h1>
    <div class="photo tone-berry" style="left:33px;top:101px;width:92px;height:82px" role="img" aria-label="Chia pudding cups topped with blueberries"></div>
    <div class="photo tone-cracker" style="left:129px;top:101px;width:93px;height:82px" role="img" aria-label="Seed crackers on baking paper"></div>
    <div class="photo tone-bread" style="left:33px;top:187px;width:92px;height:82px" role="img" aria-label="Sliced seeded loaf"></div>
    <div class="photo tone-cacao" style="left:129px;top:187px;width:93px;height:82px" role="img" aria-label="Cacao bliss balls on a plate"></div>
    <div class="badge">Rooted<br>Whole<br>Wellness</div>
    <div class="band band--bottom band--strong" style="height:21px">by Lia Marsh</div>
  </section>

  <section class="cover cover--hero">
    <div class="photo tone-bites-large" style="inset:0" role="img" aria-label="Coconut bliss balls in a glass jar"></div>
    <h1 class="title-strip">The Balanced Glow Cookbook</h1>
    <div class="badge">Rooted<br>Whole<br>Wellness</div>
    <div class="band band--bottom band--strong" style="height:21px">Lia Marsh</div>
  </section>

  <section class="cover cover--panel">
    <div class="photo tone-bites-large" style="left:24px;top:0;width:200px;height:308px" role="img" aria-label="Coconut bliss balls in a glass jar"></div>
    <div class="badge">Rooted<br>Whole<br>Wellness</div>
    <div class="info-panel">
      <p class="info-panel__kicker">HEALTHY RECIPES</p>
      <div class="info-panel__rule"></div>
      <h1 class="info-panel__title">The<br>Balanced<br>Glow<br>Cookbook</h1>
      <div class="info-panel__rule info-panel__rule--lower"></div>
      <p class="info-panel__byline">BY LIA MARSH</p>
    </div>
  </section>

</main>
</body>
</html>
```